Tech business card design

We need an amazing business card design for our new business 'Pexla' a marketing tech startup based in Sydney, Australia. We provide an online marketplace for businesses to search and buy advertising media, connect with service providers and learn more about marketing. We wish to communicate 'cool tech', reliability and professionalism and design based around our logo.

Target Market(s)

Business Owners

Contact Information for Business Card

Name
Position
Email Address
Website
Phone Number

Font styles to use
Other font styles liked:
• Avenir & Avenir Next

Colors

Designer to choose colors to be used in the design.

```html
<!DOCTYPE html>
<html lang="en">
<head>
<meta charset="utf-8">
<title>Pexla business card</title>
<link rel="stylesheet" href="https://fonts.googleapis.com/css2?family=Mulish:wght@300;400;600;800&display=swap">
<style>
  :root {
    --stage: #232323;
    --navy: #17165a;
    --navy-deep: #0d0c36;
    --navy-ink: #15143f;
    --paper: #ffffff;
    --grey: #8a8a93;
    --white: #ffffff;
  }
  * { margin: 0; padding: 0; box-sizing: border-box; }
  html, body {
    width: 1200px; height: 892px; overflow: hidden;
    background: var(--stage);
    font-family: "Mulish", "Avenir Next", Avenir, sans-serif;
  }
  .stage { position: relative; width: 1200px; height: 892px; }
  .card {
    position: absolute; width: 540px; height: 309px;
    box-shadow: 0 18px 40px rgba(0,0,0,.55);
    overflow: hidden;
  }
  .card--front {
    left: 45px; top: 170px;
    background: radial-gradient(ellipse at 45% 30%, var(--navy) 0%, var(--navy-deep) 85%);
    display: flex; flex-direction: column; align-items: center; justify-content: center;
  }
  .card--back { left: 615px; top: 413px; background: var(--paper); }
  .wordmark {
    font-weight: 800; letter-spacing: -2px; line-height: 1;
    position: relative;
  }
  .wordmark sup { font-size: 10px; font-weight: 800; letter-spacing: 0; position: absolute; top: 6px; right: -18px; }
  .card--front .wordmark { color: var(--white); font-size: 104px; }
  .front-url {
    margin-top: 26px; color: var(--white); font-size: 11px; font-weight: 400;
    letter-spacing: 6px;
  }
  .card--back .wordmark {
    position: absolute; right: 66px; top: 34px;
    color: var(--navy-ink); font-size: 72px;
  }
  .holder { position: absolute; left: 34px; bottom: 72px; }
  .holder-name { color: var(--navy-ink); font-size: 20px; font-weight: 800; line-height: 1.05; }
  .holder-role { color: var(--grey); font-size: 16px; font-weight: 400; line-height: 1.1; }
  .contact-band {
    position: absolute; left: 0; right: 0; bottom: 28px; height: 30px;
    background: var(--navy-ink); color: var(--white);
    display: flex; align-items: center; padding-left: 34px;
    font-size: 13px; font-weight: 400; white-space: nowrap;
  }
  .contact-band b { font-weight: 600; }
</style>
</head>
<body>
<main class="stage">
  <section class="card card--front" aria-label="Card front">
    <div class="wordmark">pexla<sup>TM</sup></div>
    <p class="front-url">www.pexlamedia.com.au</p>
  </section>

  <section class="card card--back" aria-label="Card back">
    <div class="wordmark">pexla<sup>TM</sup></div>
    <div class="holder">
      <p class="holder-name">DANIEL WREN</p>
      <p class="holder-role">FOUNDER, DIRECTOR</p>
    </div>
    <div class="contact-band">
      <b>P:</b>&nbsp;+61 (0)400 555 218&nbsp;<b>E:</b>&nbsp;daniel@pexlamedia.com.au&nbsp;<b>W:</b>&nbsp;pexlamedia.com.au
    </div>
  </section>
</main>
</body>
</html>
```